Brightway Haus Inc. Business Card Design

Brightway Haus Inc. is in search of a great clean design for our business cards!

Looking to incorporate our full logo and watermark on side one (however, I am open to having the text and watermark separated within the design.)

On side two, I am looking to have contact information (Name, Position, Phone #, Email, Website (www.thebrightwayhaus.ca). Can have the logo and/or watermark as part of the design if applicable.

Please add tagline "Where Shine Counts" on either side 1 or 2. This tagline can be in a sans serif, serif or cursive font as long as it compliments overall design. Capitalization can be title or sentence case depending on how it fits within the design.

Get creative!! Looking for a clean, crisp, premium design! Looking for a glossy card finish with spot UV features when printed. Cards will also be printed with rounded corners. Standard dimensions (3.5 x 2).

Target Market(s)

B2B - primary clients are business owners or property management corporations. (residential jobs are few and far between)

Industry/Entity Type

Business

Contact Information for Business Card

- clean, crisp design
- double sided
- spot UV accents and glossy finish upon printing
- standard business card size (3.5 x 2) with rounded corners
- please see project description for requirements per side

Font styles to use
Sans Serif

Requirements
Must have
• - adequate bleeds with print ready files
• - cohesive design elements between side 1 & 2
• - spot UV elements (can be on both sides or just one, use your discretion)
• - colour pallet should match the logo file provided
• - incorporate tagline "where shine counts" (this tagline can be in a serif or sans serif font as long as it is complimentary to the overall design.
Nice to have
• - Premium elements with a clean design
Should not have
• - Please omit cartoon or whimsical like designs, think premium.
• - Colours should not stray from the pallet of the provided logo.

```html
<!DOCTYPE html>
<html lang="en">
<head>
<meta charset="utf-8">
<title>Brightway Haus Inc. Business Card</title>
<link rel="stylesheet" href="https://fonts.googleapis.com/css2?family=Source+Sans+3:wght@400;600;700&display=swap">
<style>
  :root {
    --backdrop: #2a2a2a;
    --navy: #1d2553;
    --teal: #12b8bb;
    --white: #ffffff;
    --paper: #efefef;
    --grey: #a9a9a9;
  }
  * { margin: 0; padding: 0; box-sizing: border-box; }
  html, body { width: 1200px; height: 960px; overflow: hidden; }
  body {
    position: relative;
    background: var(--backdrop);
    font-family: "Source Sans 3", Arial, sans-serif;
  }
  .card {
    position: absolute;
    width: 600px;
    height: 342px;
    border-radius: 18px;
    overflow: hidden;
  }
  .card--front { left: 314px; top: 113px; background: var(--navy); color: var(--white); }
  .card--back { left: 311px; top: 472px; background: var(--paper); }

  .accent-band { position: absolute; left: 0; top: 0; }

  .front-wordmark {
    position: absolute;
    left: 30px; top: 38px;
    font-size: 27px;
    font-weight: 700;
    letter-spacing: -0.3px;
    color: var(--white);
  }
  .person { position: absolute; left: 30px; top: 120px; }
  .person__name { font-size: 16px; font-weight: 700; line-height: 20px; }
  .person__role { font-size: 16px; font-weight: 400; line-height: 20px; }
  .address { position: absolute; left: 30px; top: 170px; font-size: 15px; line-height: 19px; }
  .contact-list { position: absolute; left: 30px; top: 212px; list-style: none; font-size: 15px; line-height: 19.2px; }
  .contact-list li { display: flex; align-items: center; gap: 9px; }
  .contact-list svg { width: 13px; height: 13px; fill: var(--white); flex: none; }

  .back-wordmark {
    position: absolute;
    left: 0; right: 0; top: 142px;
    display: flex; justify-content: center; align-items: center; gap: 10px;
    font-size: 40px;
    font-weight: 700;
    letter-spacing: -0.5px;
    color: var(--navy);
  }
  .back-wordmark__mark { width: 30px; height: 30px; background: var(--teal); }
  .tagline {
    position: absolute;
    left: 100px; right: 100px; top: 277px;
    display: flex; align-items: center; gap: 4px;
    font-size: 18px; font-weight: 600; color: var(--navy);
    white-space: nowrap;
  }
  .tagline__rule { flex: 1; height: 1px; }
  .tagline__rule--left { background: linear-gradient(to right, transparent, var(--navy)); }
  .tagline__rule--right { background: linear-gradient(to left, transparent, var(--navy)); }
  .tagline__accent { color: var(--teal); }
</style>
</head>
<body>

<section class="card card--front" aria-label="Business card front">
  <svg class="accent-band" width="600" height="342" viewBox="0 0 600 342" aria-hidden="true">
    <polygon points="344,0 600,0 600,150 316,282" fill="var(--teal)"/>
    <polygon points="600,150 600,172 330,300 316,282" fill="var(--white)"/>
  </svg>

  <div class="front-wordmark">BRIGHTWAY HAUS INC.</div>

  <div class="person">
    <p class="person__name">MARA ELLISON</p>
    <p class="person__role">CEO/FOUNDER</p>
  </div>

  <p class="address">4120 Larchmont Road<br>Halden, Ontario K2P 4R8</p>

  <ul class="contact-list">
    <li><svg viewBox="0 0 16 16"><path d="M1 5c0-2 3-3 7-3s7 1 7 3v1h-4V5H5v1H1zM3 7h10l1 7H2z"/></svg>613 555 0142</li>
    <li><svg viewBox="0 0 16 16"><path d="M4 0h8v16H4zM5.5 2v10h5V2z"/></svg>613 555 0187</li>
    <li><svg viewBox="0 0 16 16"><path d="M4 1h8v4H4zM1 6h14v6h-3v3H4v-3H1zM5 10v3h6v-3z"/></svg>613 555 0193</li>
    <li><svg viewBox="0 0 16 16"><path d="M1 3h14L8 9zM1 5l7 5 7-5v8H1z"/></svg>mara@thebrightwayhaus.ca</li>
    <li><svg viewBox="0 0 16 16"><circle cx="8" cy="8" r="7"/></svg>www.thebrightwayhaus.ca</li>
  </ul>
</section>

<section class="card card--back" aria-label="Business card back">
  <div class="back-wordmark">
    <span class="back-wordmark__mark"></span>
    <span>BRIGHTWAY HAUS INC.</span>
  </div>
  <p class="tagline">
    <span class="tagline__rule tagline__rule--left"></span>
    <span>Where <span class="tagline__accent">Shine</span> Counts</span>
    <span class="tagline__rule tagline__rule--right"></span>
  </p>
</section>

</body>
</html>
```